Flyer-Design für Tannbergs Hotel
Zielgruppe
Tannbergs Hotel
Aufgabenstellung
Texte: siehe alten Fyler,
drei Sterne dürfen nicht mehr in den Texten auftauchen.
www.lindners-hotel-beispiel.de

```html
<!DOCTYPE html>
<html lang="de">
<head>
<meta charset="utf-8">
<title>Tannbergs Hotel Garni – Flyer</title>
<link href="https://fonts.googleapis.com/css2?family=Open+Sans:wght@400;600&family=Pinyon+Script&display=swap" rel="stylesheet">
<style>
  :root {
    --gold: #a67f33;
    --gold-text: #9b742a;
    --white: #ffffff;
    --ink: #3a3a3a;
    --wood-light: #e8c9a6;
    --wood-dark: #b08866;
  }
  html, body { margin: 0; padding: 0; overflow: hidden; background: var(--white); }
  .flyer {
    position: relative; width: 1200px; height: 423px; overflow: hidden;
    font-family: "Open Sans", Arial, sans-serif; color: var(--ink);
  }
  .script { font-family: "Pinyon Script", cursive; font-weight: 400; }
  .abs { position: absolute; white-space: nowrap; }

  /* Inside left page */
  .welcome-band { left: 0; top: 0; width: 600px; height: 102px; background: var(--gold); }
  .welcome-frame { left: 18px; top: 14px; width: 566px; height: 75px; border: 1px solid var(--white); box-sizing: border-box; }
  .welcome-kicker { left: 37px; top: 27px; color: var(--white); font-size: 14px; letter-spacing: 0.2px; }
  .welcome-name { left: 114px; top: 46px; color: var(--white); font-size: 30px; line-height: 1; }
  .band-brand { left: 462px; top: 45px; display: flex; align-items: center; gap: 6px; color: var(--white); font-size: 12px; font-weight: 600; }
  .band-brand .dot { width: 14px; height: 14px; border-radius: 50%; background: var(--white); }

  .section-title { left: 175px; top: 108px; color: var(--gold-text); font-size: 19px; line-height: 40px; }
  .section-title .cap { font-family: "Pinyon Script", cursive; font-size: 38px; }

  .room-photo { height: 120px; width: 140px; }
  .photo-single { left: 18px; top: 154px; height: 117px; background: linear-gradient(135deg, #e9ecef, #ffffff 55%, #c9ccd0); }
  .photo-double { left: 167px; top: 151px; background: linear-gradient(180deg, #f3eef0 0%, #f7e9ec 55%, #d8305a 80%, #c03050 100%); }
  .photo-apartment { left: 317px; top: 151px; height: 118px; background: linear-gradient(135deg, #8b8a86, #c7c3bb 50%, #a57a4a 100%); }

  .room-title { top: 286px; width: 140px; text-align: center; color: var(--gold-text); font-size: 8.3px; line-height: 10.2px; }
  .room-text { top: 314px; width: 140px; font-size: 8.7px; line-height: 10.2px; color: var(--ink); white-space: normal; margin: 0; }
  .room-price { top: 372px; color: var(--gold-text); font-size: 14px; }
  .footnote { left: 23px; top: 399px; font-size: 6px; color: var(--gold-text); }

  .extras-title { left: 466px; top: 109px; width: 118px; text-align: center; color: var(--gold-text); font-size: 16px; line-height: 18px; }
  .extras-box { left: 466px; top: 151px; width: 118px; height: 258px; background: var(--gold); }
  .extras-list { list-style: none; margin: 0; padding: 12px 0 0 15px; color: var(--white); font-size: 8.7px; line-height: 18.1px; }

  /* Cover page */
  .cover { left: 600px; top: 0; width: 232px; height: 423px; background: var(--gold); }
  .cover-frame { left: 612px; top: 14px; width: 211px; height: 396px; border: 2px solid var(--white); box-sizing: border-box; }
  .cover-brand { left: 612px; top: 62px; width: 211px; display: flex; flex-direction: column; align-items: center; gap: 10px; color: var(--white); }
  .cover-brand .name { font-size: 18px; font-weight: 600; }
  .cover-brand .dot { width: 22px; height: 22px; border-radius: 50%; background: var(--white); }
  .claim { color: var(--white); font-size: 19px; line-height: 44px; }
  .claim .cap { font-family: "Pinyon Script", cursive; font-size: 42px; }
  .claim-1 { left: 624px; top: 200px; }
  .claim-2 { left: 682px; top: 234px; }
  .cover-name { left: 612px; top: 317px; width: 211px; text-align: center; color: var(--white); font-size: 20px; line-height: 24px; }
  .cover-address { left: 612px; top: 344px; width: 211px; text-align: center; color: var(--white); font-size: 8.5px; line-height: 10.2px; }

  /* Back page image */
  .welcome-photo { left: 832px; top: 0; width: 368px; height: 423px;
    background: linear-gradient(160deg, #eef3ea 0%, #cfe3b5 12%, var(--wood-light) 30%, var(--wood-dark) 60%, #d9b08a 100%); }
</style>
</head>
<body>
<div class="flyer">
  <div class="abs welcome-band"></div>
  <div class="abs welcome-frame"></div>
  <div class="abs welcome-kicker">HERZLICH WILLKOMMEN IM</div>
  <div class="abs welcome-name script">Tannbergs Hotel Garni</div>
  <div class="abs band-brand"><span>Tannbergs Hotel</span><span class="dot"></span></div>

  <div class="abs section-title"><span class="cap">P</span>reise <span class="cap">&amp;</span> <span class="cap">Z</span>immer</div>

  <div class="abs room-photo photo-single" role="img" aria-label="Foto: helles Einzelzimmer mit Nachttischlampe"></div>
  <div class="abs room-photo photo-double" role="img" aria-label="Foto: Doppelzimmer mit rotem Teppich und Dachfenstern"></div>
  <div class="abs room-photo photo-apartment" role="img" aria-label="Foto: Appartment mit Hängelampe und Blumen auf dem Tisch"></div>

  <div class="abs room-title" style="left:10px">EINZELZIMMER*</div>
  <div class="abs room-title" style="left:167px">DOPPEL- ODER<br>ZWEIBETTZIMMER*</div>
  <div class="abs room-title" style="left:312px">APPARTMENT*</div>

  <p class="abs room-text" style="left:23px">EinzelzimmerBus, qui sero et et arios mo erspelit que volupta de­nis ratus dus id modic teste conse quatis. volupta denis ratus dus id modic teste conse quatis.</p>
  <p class="abs room-text" style="left:167px">EinzelzimmerBus, qui sero et et arios mo erspelit que volupta de­nis ratus dus id modic teste conse quatis. volupta denis ratus dus id modic teste conse quatis.</p>
  <p class="abs room-text" style="left:317px">EinzelzimmerBus, qui sero et et arios mo erspelit que volupta de­nis ratus dus id modic teste conse quatis. volupta denis ratus dus id modic teste conse quatis.</p>

  <div class="abs room-price script" style="left:23px">00,00 Euro</div>
  <div class="abs room-price script" style="left:167px">00,00 Euro</div>
  <div class="abs room-price script" style="left:317px">00,00 Euro</div>

  <div class="abs footnote">*Haustiere sind nicht gestattet.</div>

  <div class="abs extras-title script">weitere<br>Annehmlichkeiten</div>
  <div class="abs extras-box">
    <ul class="extras-list">
      <li>WLAN kostenfrei</li>
      <li>Private Parkplätze</li>
      <li>Minimarkt vor Ort</li>
      <li>Sanckautomat</li>
      <li>Getränkeautomat</li>
      <li>Nichtraucherzimmer</li>
      <li>Schuhputzmaschine</li>
      <li>Schuhputzservice</li>
      <li>Express Check-in/-out</li>
      <li>Aufzug</li>
      <li>Fahrradverleih</li>
      <li>Safe</li>
      <li>Zeitungen</li>
    </ul>
  </div>

  <div class="abs cover"></div>
  <div class="abs cover-frame"></div>
  <div class="abs cover-brand"><span class="name">Tannbergs Hotel</span><span class="dot"></span></div>
  <div class="abs claim claim-1"><span class="cap">K</span>omfort</div>
  <div class="abs claim claim-2"><span class="cap">&amp;</span> <span class="cap">T</span>radition</div>
  <div class="abs cover-name script">Tannbergs Hotel Garni</div>
  <div class="abs cover-address">
    Jonas Tannberg<br>
    Birkenallee 7<br>
    12345 Musterstadt<br>
    Telefon: +49 (0) 1234-567890<br>
    Telefax: +49 (0) 1234-567891
  </div>

  <div class="abs welcome-photo" role="img" aria-label="Foto: Holzschild mit der Aufschrift Welcome vor grünem Laub"></div>
</div>
</body>
</html>
```